Pemberlux: Smart Quotes for Wine Lovers

Hello. I am completing book of quotes for wine lovers. Need the text formatted so that it is easy to read and aesthetically pleasing...modern, clean, smart. Number the pages. The cover is complete. Book is small square. 7.5 by 7.5 inches. If you want to show me first few pages that would be awesome. Thank you!
Updates

I edited the quotes so if you downloaded first ones, please grab these ones instead, thank you! 

Target Market(s)

wine lovers. Urban. Modern.

Industry/Entity Type

Quotes

Requirements
Should not have
• No color. black and white only.

```html
<!DOCTYPE html>
<html lang="en">
<head>
<meta charset="utf-8">
<title>Pemberlux: Smart Quotes for Wine Lovers</title>
<link rel="stylesheet" href="https://fonts.googleapis.com/css2?family=Jost:wght@400;500;700&display=swap">
<style>
  :root {
    --backdrop: #e4e4e4;
    --paper: #ffffff;
    --ink: #111111;
    --rule: #222222;
    --glass-tone: #d2d2d2;
  }
  * { box-sizing: border-box; margin: 0; padding: 0; }
  html, body {
    width: 1200px;
    height: 900px;
    overflow: hidden;
    background: var(--backdrop);
    font-family: "Jost", sans-serif;
    color: var(--ink);
  }
  .spread {
    position: absolute;
    left: 60px;
    top: 187px;
    width: 1064px;
    height: 529px;
    display: flex;
    background: var(--paper);
    border: 1px solid var(--rule);
  }
  .page {
    position: relative;
    width: 50%;
    height: 100%;
  }
  .page + .page { border-left: 1px solid var(--rule); }
  .quote {
    position: absolute;
    top: 52px;
    left: 76px;
    right: 76px;
    text-align: center;
    font-size: 23px;
    font-weight: 500;
    line-height: 34px;
  }
  .quote--short { top: 86px; }
  .quote-author {
    display: block;
    font-weight: 700;
  }
  .glass-art {
    position: absolute;
    top: 200px;
    left: 50%;
    width: 72px;
    height: 166px;
    margin-left: -31px;
    background: linear-gradient(180deg, #e6e6e6 0%, var(--glass-tone) 60%, #dcdcdc 100%);
    border-radius: 6px;
  }
  .bio {
    position: absolute;
    top: 391px;
    left: 98px;
    right: 98px;
    text-align: center;
    font-size: 12.5px;
    line-height: 17px;
  }
  .bio-name { font-weight: 700; }
  .page-number {
    position: absolute;
    top: 487px;
    left: 0;
    right: 0;
    text-align: center;
    font-size: 12.5px;
    font-weight: 700;
  }
</style>
</head>
<body>
  <main class="spread">
    <section class="page">
      <p class="quote">The discovery of a good wine is increasingly better for mankind than the discovery of a new star.
        <span class="quote-author">– Aurelio Montavi</span></p>
      <div class="glass-art" role="img" aria-label="Two overlapping grey wine glasses"></div>
      <p class="bio"><span class="bio-name">Aurelio Montavi</span> (1631 –1698)<br>
        Venetian Baroque Painter, Vintner, Poet, Musician, Glassmaker, Botanist, Engineer, Traveller, Cartographer and Writer.</p>
      <p class="page-number">-1-</p>
    </section>
    <section class="page">
      <p class="quote quote--short">Be careful to trust a person who does not like wine.
        <span class="quote-author">– Konrad Halvers</span></p>
      <div class="glass-art" role="img" aria-label="Two overlapping grey wine glasses"></div>
      <p class="bio"><span class="bio-name">Konrad Halvers (1822 –1879)</span><br>
        Bavarian Essayist, Vintner, Cellar Master, Historian, Journalist, and Travelling Lecturer.</p>
      <p class="page-number">-2-</p>
    </section>
  </main>
</body>
</html>
```